Business card design needed

I would like a one sided black business card with the information provided above. Refer to my website www.brightvolleyracquets.com.au for an example of colors I have used for my site, would like to keep this consistent for my business cards also, I will upload my logo below.

I am a new small business that provides tennis customers with racquet re stringing, tennis strings and accessories.

Industry/Entity Type

Small Business

Contact Information for Business Card

Bright Volley Tennis

Owen Whitby
Managing Director

brightvolleyracquets@mailbox.example
www.brightvolleyracquets.com.au
0491 726 305

Racquet Restringing/Tennis Strings/Accessories

Requirements
Must have
• Must have my logo and card must be black

```html
<!DOCTYPE html>
<html lang="en">
<head>
<meta charset="utf-8">
<title>Bright Volley Tennis – Business Card</title>
<link href="https://fonts.googleapis.com/css2?family=Aldrich&display=swap" rel="stylesheet">
<style>
  :root {
    --page-bg: #e9e6e1;
    --card-black: #050505;
    --lime: #8cc63f;
    --lime-text: #c6e43a;
    --royal: #2a58a8;
    --navy: #1d2f78;
    --white: #f2f2f2;
    --email-blue: #4f7fe0;
  }
  * { margin: 0; padding: 0; box-sizing: border-box; }
  html, body {
    width: 1200px; height: 800px; overflow: hidden;
    background: var(--page-bg);
    font-family: "Aldrich", sans-serif;
  }
  .business-card {
    position: absolute; left: 100px; top: 110px;
    width: 1000px; height: 580px;
    background: var(--card-black);
    border-radius: 40px;
    overflow: hidden;
    box-shadow: 0 12px 30px rgba(0,0,0,.25);
  }
  .card-swoosh { position: absolute; inset: 0; width: 100%; height: 100%; }
  .brand {
    position: absolute; left: 70px; top: 300px;
    display: flex; align-items: center; gap: 16px;
  }
  .brand-dot {
    width: 46px; height: 46px; border-radius: 50%;
    background: var(--lime);
  }
  .brand-name {
    font-size: 34px; color: var(--lime-text);
    text-transform: uppercase; letter-spacing: 1px;
  }
  .contact {
    position: absolute; right: 215px; top: 80px;
    text-align: right;
  }
  .contact-name {
    font-size: 40px; color: var(--white);
    text-transform: uppercase; letter-spacing: 1px; line-height: 1;
  }
  .contact-title {
    font-size: 15px; color: var(--white); margin-top: 6px;
  }
  .contact-line {
    display: flex; align-items: center; justify-content: flex-end;
    gap: 8px; margin-top: 6px; font-size: 19px;
  }
  .contact-line svg { width: 16px; height: 16px; flex: none; }
  .contact-phone { color: var(--white); margin-top: 8px; }
  .contact-email { color: var(--email-blue); font-size: 17px; margin-top: 34px; }
  .contact-web { color: var(--lime-text); font-size: 17px; padding-right: 24px; }
</style>
</head>
<body>
  <div class="business-card">
    <svg class="card-swoosh" viewBox="0 0 1000 580" preserveAspectRatio="none" aria-hidden="true">
      <defs>
        <linearGradient id="blue-sweep" x1="0" y1="1" x2="1" y2="0">
          <stop offset="0" stop-color="var(--royal)"/>
          <stop offset="1" stop-color="var(--navy)"/>
        </linearGradient>
      </defs>
      <path d="M250 580 C520 500 830 330 1000 30 L1000 580 Z" fill="var(--lime)"/>
      <path d="M300 580 C560 520 860 370 1000 120 L1000 580 Z" fill="url(#blue-sweep)"/>
      <path d="M262 580 C530 504 838 340 1000 55" fill="none" stroke="var(--card-black)" stroke-width="4"/>
      <path d="M282 580 C545 512 848 352 1000 85" fill="none" stroke="var(--card-black)" stroke-width="2"/>
    </svg>

    <div class="brand">
      <span class="brand-dot"></span>
      <span class="brand-name">Bright Volley Tennis</span>
    </div>

    <div class="contact">
      <p class="contact-name">Owen Whitby</p>
      <p class="contact-title">Managing Director</p>
      <p class="contact-line contact-phone">+ 0491 726 305
        <svg viewBox="0 0 16 16"><path d="M4 1l3 3-1.6 1.8a9 9 0 0 0 4.8 4.8L12 9l3 3-2 2.5C7 14 2 9 1.5 3z" fill="var(--white)"/></svg>
      </p>
      <p class="contact-line contact-email">brightvolleyracquets@mailbox.example
        <svg viewBox="0 0 16 16"><rect x="1" y="3" width="14" height="10" rx="1" fill="var(--lime-text)"/><path d="M1 4l7 5 7-5" fill="none" stroke="var(--card-black)" stroke-width="1.4"/></svg>
      </p>
      <p class="contact-line contact-web">www.brightvolleyracquets.com.au</p>
    </div>
  </div>
</body>
</html>
```